Digital Marketing Website Redesign, modern, fresh, dynamic

Hi there, we would like to freshen up our website and create a new dynamic look. We are a digital marketing agency who specialise in digital transformation in the form of creating websites for appointment bookings. Our clients are service businesses such as hairdressers, dentists and doctors who's patients need to book appointments with them.

Our company name is Tallomex with the point being we can help increase your revenue curve by increasing your appointment bookings.

Our services include building the website, creating campaigns to drive traffic, increasing conversions and monitoring and reporting.

We are playing with a tagline of 'Step into your Digital Transformation' as we have a 5 step journey that customers can take with us getting them from zero to full appointment bookings.

Our current website is www.tallomex-sample.com

You can see a draft design that I mocked up on Canva here https://www.draftboard-sample.com/design/QXB82LmpR7T/KpoW39dnFsYbZet_wqe_OPa/edit?utm_content=QXB82LmpR7T&utm_campaign=designshare&utm_medium=link2&utm_source=sharebutton

Also attached some other homepage ideas. In regard to photos we are open to ideas.

Please let if you need any more information to provide us with an initial design. Thanks million and I look forward to receiving fantastic designs :)

Marian Dobbs
Tallomex

Target Market(s)

Appointment based businesses such as hairdressers, dentists, doctors

Industry/Entity Type

Marketing and Digital

Coding

Coded - Design and coding required

Number of Pages Required

1 page

Colors
0094D4
00A9DD
6FCCEA
C7EBF8
E9F6FB

Requirements
Must have
• Appointment booking CTA
Nice to have
• A website we like https://www.fergalwhitty-sample.ie

```html
<!DOCTYPE html>
<html lang="en">
<head>
<meta charset="utf-8">
<title>Tallomex – Digital Marketing</title>
<link href="https://fonts.googleapis.com/css2?family=Fira+Sans:wght@500;600;700&family=Poppins:wght@400;500;600;700&family=Roboto:wght@700&display=swap" rel="stylesheet">
<style>
:root{
  --navy:#1c3a6e;
  --ink:#1b1f33;
  --deep:#101a44;
  --accent:#0094d4;
  --accent-bright:#00a9dd;
  --accent-soft:#6fccea;
  --accent-pale:#c7ebf8;
  --accent-mist:#e9f6fb;
  --grey-bg:#e9f6fb;
  --text:#6b7080;
  --white:#ffffff;
  --phone-blue:#2d4f86;
}
*{margin:0;padding:0;box-sizing:border-box}
html,body{width:1200px;height:4837px;overflow:hidden;background:var(--white)}
body{font-family:"Poppins",sans-serif;color:var(--ink);position:relative}
.abs{position:absolute}
h1,h2,h3{font-family:"Fira Sans",sans-serif}
.btn{position:absolute;background:var(--accent);color:var(--white);font-weight:600;font-size:15px;display:flex;align-items:center;justify-content:center;gap:10px;border-radius:2px;white-space:nowrap}
.label{position:absolute;font-size:12px;font-weight:500;color:var(--accent);letter-spacing:.5px;text-decoration:underline;text-underline-offset:4px}
.sec-title{position:absolute;font-size:40px;font-weight:600;color:var(--navy)}

/* top bar */
.topbar{top:0;left:0;width:1200px;height:47px;background:var(--ink);color:#d7d9e2;font-size:13px}
.topbar .info{left:78px;top:15px;display:flex;gap:30px}
.topbar .links{left:870px;top:15px;display:flex;gap:16px}
.topbar .social{left:1036px;top:17px;display:flex;gap:14px}
.topbar .social span{width:11px;height:11px;border-radius:50%;background:#9ea2b3;display:block}

/* header */
.brand{font-family:"Poppins",sans-serif;font-weight:700;color:var(--navy);font-size:34px;display:flex;align-items:center;gap:8px}
.brand i{width:14px;height:14px;border-radius:50%;background:var(--accent);display:block}
.head-brand{left:73px;top:76px}
.head-item{top:78px;display:flex;gap:14px;align-items:center;font-size:13px}
.head-item b{display:block;font-weight:500;color:var(--ink)}
.head-item small{display:block;color:var(--text);font-size:12px}
.estimate{left:958px;top:75px;width:180px;height:50px;font-size:13px}

/* nav */
.nav{left:78px;top:155px;width:987px;height:67px;background:var(--white);display:flex;align-items:center;z-index:3}
.nav a{font-size:13px;color:#555a6a;text-decoration:none;padding:0 40px 0 88px;margin-left:-50px}
.nav a:first-child{margin-left:0}
.nav-phone{left:1065px;top:155px;width:73px;height:67px;background:var(--phone-blue);z-index:3;display:flex;align-items:center;justify-content:center}

/* hero */
.hero{top:155px;left:0;width:1200px;height:800px;background:linear-gradient(160deg,#0c2b3a 0%,#0f4a5e 40%,#12667a 60%,#0a2130 100%)}
.hero-curve{top:840px;left:0}
.tag{left:100px;width:222px;height:44px;background:var(--navy);border-left:4px solid var(--accent-bright);color:var(--white);font-family:"Roboto",sans-serif;font-size:20px;font-weight:700;padding:10px 18px}
.hero h1{position:absolute;left:100px;font-family:"Roboto",sans-serif;font-size:54px;color:var(--white)}
.hero-text{left:100px;width:520px;color:var(--white);font-size:16px;line-height:26px}
.hero-btn{left:100px;width:175px;height:50px}

/* about */
.about .label{left:82px;top:1064px}
.about h2{position:absolute;left:82px;top:1098px;font-size:40px;font-weight:600;line-height:54px;color:var(--navy)}
.about h3{position:absolute;left:82px;top:1228px;font-size:22px;font-weight:500;color:var(--navy)}
.about p{position:absolute;left:82px;top:1274px;width:505px;font-size:12px;line-height:22px;color:var(--text)}
.about-btn{left:82px;top:1432px;width:155px;height:46px;font-size:14px}
.photo-a{left:617px;top:1047px;width:237px;height:426px;background:linear-gradient(180deg,#c8ccd0,#6f6458 55%,#2d2c2c)}
.photo-b{left:871px;top:1078px;width:236px;height:425px;background:linear-gradient(180deg,#aab0b7,#5c6470 60%,#2b2f36)}
.badge{left:820px;top:1235px;width:80px;height:80px;border-radius:50%;background:var(--navy);border:4px solid var(--white);display:flex;align-items:center;justify-content:center;color:var(--white);font-size:12px;font-weight:600}

/* services */
.services{top:1560px;left:0;width:1200px;height:650px;background:var(--grey-bg)}
.services .label{left:86px;top:62px}
.services .sec-title{left:86px;top:95px}
.more{left:942px;top:110px;font-size:14px;color:var(--navy);font-weight:500}
.more-arrow{left:1075px;top:102px;width:40px;height:38px;background:var(--accent);display:flex;align-items:center;justify-content:center}
.card{position:absolute;top:210px;width:318px;height:352px;border-radius:4px;overflow:hidden}
.card .fill{position:absolute;inset:0}
.card h3{position:absolute;left:28px;top:235px;color:var(--white);font-size:25px;font-weight:600}
.card .go{position:absolute;left:28px;top:285px;width:46px;height:46px;border-radius:50%;background:rgba(255,255,255,.25);display:flex;align-items:center;justify-content:center}

/* experts */
.experts-band{top:2210px;left:0;width:1200px;height:385px;background:linear-gradient(120deg,#0f3a7a,#1d4c92 45%,#122d63)}
.experts-band h2{position:absolute;left:90px;top:106px;color:var(--white);font-size:40px;font-weight:600;line-height:54px}
.experts-btn{left:90px;top:275px;width:152px;height:46px;font-size:14px}
.exp-card{position:absolute;top:2322px;width:234px;height:366px;background:var(--white);box-shadow:0 6px 22px rgba(20,30,60,.12);text-align:center}
.exp-card svg{margin-top:24px}
.exp-card h3{font-family:"Poppins",sans-serif;font-size:20px;font-weight:500;color:var(--navy);margin-top:20px}
.exp-card p{font-size:12px;line-height:19px;color:var(--text);width:190px;margin:24px auto 0}
.exp-card .more-link{display:block;margin-top:28px;font-size:13px;font-weight:600;color:var(--navy)}

/* why */
.why .label{left:573px;top:2740px}
.why .sec-title{left:0;width:1200px;top:2775px;text-align:center}
.portrait{left:434px;top:2909px;width:326px;height:326px;border-radius:50%;background:radial-gradient(circle at 50% 40%,#9aa2b5,#3a4f7e 70%,#1f3360)}
.feat{position:absolute;width:240px}
.feat h3{font-family:"Poppins",sans-serif;font-size:19px;font-weight:500;color:var(--navy)}
.feat p{font-size:12px;line-height:18px;color:var(--text);margin-top:6px}
.feat.l{text-align:right}
.ficon{position:absolute;width:78px;height:78px;border-radius:50%;background:var(--white);box-shadow:0 4px 18px rgba(20,30,60,.12);display:flex;align-items:center;justify-content:center}

/* testimonials */
.reviews{top:3335px;left:0;width:1200px;height:575px;background:linear-gradient(180deg,#0f1b47,#0c1a40)}
.reviews .label{left:551px;top:60px;color:var(--accent-soft)}
.reviews .sec-title{left:0;width:1200px;top:95px;text-align:center;color:var(--white)}
.rev{position:absolute;top:213px;width:320px;height:217px;background:#232d54;border-radius:3px;padding:58px 30px 0}
.rev .q{position:absolute;left:142px;top:10px}
.rev p{font-size:13px;line-height:19px;color:#e3e6f0}
.rev .who{display:flex;align-items:center;gap:14px;margin-top:12px}
.rev .av{width:48px;height:48px;border-radius:50%;background:linear-gradient(#d8d2cc,#a59a91)}
.rev .who b{display:block;font-size:15px;font-weight:500;color:var(--white)}
.rev .who small{display:block;font-size:14px;color:#8890aa}
.dots{left:567px;top:458px;display:flex;gap:8px}
.dots span{width:6px;height:6px;border-radius:50%;background:#7c84a6}
.dots span.on{background:var(--accent-bright)}

/* contact */
.contact h2{position:absolute;left:101px;top:3980px;font-size:38px;font-weight:600;color:var(--navy)}
.c-item{position:absolute;left:110px;display:flex;gap:24px;align-items:flex-start}
.c-item b{display:block;font-size:12px;font-weight:600;color:var(--navy)}
.c-item small{display:block;font-size:12px;color:var(--text)}
.footer-wave{top:4330px;left:0}
.form{left:597px;top:3975px;width:493px;height:570px;background:var(--white);border-top:5px solid var(--navy);box-shadow:0 8px 30px rgba(20,30,60,.12);padding:38px 36px;z-index:2}
.form h3{font-family:"Poppins",sans-serif;font-size:24px;font-weight:500;color:var(--navy)}
.field{position:absolute}
.field label{display:block;font-size:12px;font-weight:600;color:var(--navy);margin-bottom:8px}
.field .box{border:1px solid #c9ccd4;border-radius:22px;height:44px;font-size:12px;color:#8a8e9a;padding:13px 24px}
.field .area{border-radius:14px;height:122px}
.form-btn{left:38px;top:474px;width:155px;height:44px;font-size:14px}

/* footer */
.footer{top:4500px;left:0;width:1200px;height:337px;background:var(--deep)}
.foot-brand{left:150px;top:118px}
.foot-brand .brand{color:var(--accent);font-size:46px}
.f-item{position:absolute;top:120px;display:flex;gap:12px;align-items:center;color:var(--white);font-size:13px;line-height:18px}
.f-nav{left:256px;top:195px;width:690px;height:50px;border-top:1px solid #3a4470;border-bottom:1px solid #3a4470;display:flex;justify-content:space-around;align-items:center;color:var(--white);font-size:14px}
.copy{left:147px;top:303px;font-size:11px;color:var(--white)}
.f-social{left:932px;top:298px;display:flex;gap:10px}
.f-social span{width:24px;height:24px;border:1px solid #c8cbe0;border-radius:3px;display:block}
</style>
</head>
<body>

<!-- top bar -->
<div class="abs topbar">
  <div class="abs info"><span>◷ Mon-Sat: 09am to 07:30pm</span><span>✉ hello@tallomex-sample.com</span></div>
  <div class="abs links"><span>|</span><span>Faqs</span><span>|</span><span>Pricing</span></div>
  <div class="abs social"><span></span><span></span><span></span><span></span></div>
</div>

<!-- header -->
<div class="abs head-brand brand">Tallomex<i></i></div>
<div class="abs head-item" style="left:360px">
  <svg width="34" height="34" viewBox="0 0 34 34"><path d="M17 5a12 11 0 1 0 0 22l-7 4 2-6A12 11 0 0 1 17 5z" fill="none" stroke="#1c3a6e" stroke-width="2"/><circle cx="12" cy="16" r="1.5" fill="#1c3a6e"/><circle cx="17" cy="16" r="1.5" fill="#1c3a6e"/><circle cx="22" cy="16" r="1.5" fill="#1c3a6e"/></svg>
  <div><b>+44-555-01-2299</b><small>Needhelp? Make a Call</small></div>
</div>
<div class="abs head-item" style="left:660px">
  <svg width="34" height="34" viewBox="0 0 34 34" fill="none" stroke="#1c3a6e" stroke-width="1.8"><circle cx="17" cy="17" r="13"/><ellipse cx="17" cy="17" rx="6" ry="13"/><path d="M4 17h26M6 10h22M6 24h22"/></svg>
  <div><b>City, Country</b><small>123A Someplace</small></div>
</div>
<div class="btn estimate">Book Appointment
  <svg width="20" height="20" viewBox="0 0 20 20" fill="none" stroke="#fff" stroke-width="1.6"><circle cx="10" cy="10" r="8.5"/><path d="M8 6l4 4-4 4"/></svg>
</div>

<!-- hero -->
<div class="abs hero" role="img" aria-label="Person walking down a glowing digital data tunnel">
  <div class="abs tag" style="top:293px">Digital Marketing</div>
  <h1 style="top:360px">Elevate Your Brand</h1>
  <p class="abs hero-text" style="top:455px">Lorem ipsum dolor sit amet, consectetur adipiscing elit, sed do eiusmod tempor incididunt ut labore et d</p>
  <div class="btn hero-btn" style="top:535px">Learn More</div>
</div>
<svg class="abs hero-curve" width="1200" height="120" viewBox="0 0 1200 120">
  <path d="M0 80 Q600 70 1200 0 V120 H0Z" fill="#fff"/>
  <path d="M0 88 Q350 90 700 55 Q420 100 0 115Z" fill="#0094d4"/>
</svg>
<nav class="abs nav">
  <a>HOME</a><a>About Us</a><a>Services</a><a>Our team</a><a>Blog</a><a>Gallery</a><a>Contact Us</a>
</nav>
<div class="abs nav-phone">
  <svg width="34" height="34" viewBox="0 0 24 24" fill="none" stroke="#fff" stroke-width="1.5"><path d="M5 3h4l2 5-2.5 1.5a11 11 0 0 0 6 6L16 13l5 2v4a2 2 0 0 1-2 2A17 17 0 0 1 3 5a2 2 0 0 1 2-2z"/></svg>
</div>

<!-- about -->
<section class="about">
  <span class="label">ABOUT US</span>
  <h2>Smart Solutions,<br>Digital Evolution</h2>
  <h3>Transforming Challenges into Triumphs</h3>
  <p>Lorem ipsum dolor sit amet, consectetur adipiscing elit, sed do eiusmod tempor incididunt ut labore et dolore magna aliqua. Ut enim ad minim veniam, quis nos trud exercitation ullamco laboris nisi ut aliquip ex ea commodo consequat. Duis aute irure dolor in reprehenderit in voluptate velit esse cillum dolore eu fugiat nulla pariatur. Excepteur sint occaecat cupidatat non proident, sunt in culpa qui officia deserunt mollit anim id est laborum.</p>
  <div class="btn about-btn">Learn More
    <svg width="16" height="12" viewBox="0 0 16 12" fill="none" stroke="#fff" stroke-width="1.8"><path d="M1 6h13M9 1l5 5-5 5"/></svg>
  </div>
  <div class="abs photo-a" role="img" aria-label="Man in glasses pointing at a computer screen"></div>
  <div class="abs photo-b" role="img" aria-label="Laptop with floating digital marketing icons"></div>
  <div class="abs badge">Tallomex</div>
</section>

<!-- services -->
<section class="abs services">
  <span class="label">OUR SERVICES</span>
  <h2 class="sec-title">Our Services</h2>
  <span class="abs more">More Services</span>
  <div class="abs more-arrow"><svg width="12" height="14" viewBox="0 0 12 14" fill="none" stroke="#fff" stroke-width="2"><path d="M3 2l6 5-6 5"/></svg></div>

  <div class="card" style="left:96px">
    <div class="fill" role="img" aria-label="Hand touching a digital marketing interface" style="background:linear-gradient(180deg,#3b4c55,#2d5f66 55%,#167a80)"></div>
    <h3>Marketing Services</h3>
    <div class="go"><svg width="16" height="12" viewBox="0 0 16 12" fill="none" stroke="#fff" stroke-width="1.8"><path d="M1 6h13M9 1l5 5-5 5"/></svg></div>
  </div>
  <div class="card" style="left:442px">
    <div class="fill" role="img" aria-label="Hands typing on a laptop with booking app graphics" style="background:linear-gradient(180deg,#2a4a66,#2c6270 55%,#167a80)"></div>
    <h3>Online Booking Apps</h3>
    <div class="go"><svg width="16" height="12" viewBox="0 0 16 12" fill="none" stroke="#fff" stroke-width="1.8"><path d="M1 6h13M9 1l5 5-5 5"/></svg></div>
  </div>
  <div class="card" style="left:788px">
    <div class="fill" role="img" aria-label="Team reviewing marketing charts at a table" style="background:linear-gradient(180deg,#b9bec3,#6c8a8e 55%,#167a80)"></div>
    <h3>Services Marketing</h3>
    <div class="go"><svg width="16" height="12" viewBox="0 0 16 12" fill="none" stroke="#fff" stroke-width="1.8"><path d="M1 6h13M9 1l5 5-5 5"/></svg></div>
  </div>
</section>

<!-- experts -->
<section class="abs experts-band" role="img" aria-label="Abstract blue network of connected points">
  <h2>Leading<br>Experts</h2>
  <div class="btn experts-btn">Contact us
    <svg width="16" height="12" viewBox="0 0 16 12" fill="none" stroke="#fff" stroke-width="1.8"><path d="M1 6h13M9 1l5 5-5 5"/></svg>
  </div>
</section>
<div class="exp-card" style="left:353px">
  <svg width="48" height="56" viewBox="0 0 48 56" fill="none" stroke="#0094d4" stroke-width="2.5"><path d="M20 30V8a4 4 0 0 1 8 0v16l10 3a5 5 0 0 1 3 6l-4 14H20l-8-12a4 4 0 0 1 6-5z"/></svg>
  <h3>Professional</h3>
  <p>Lorem ipsum dolor sit amet, consectetur adipiscing elit, sed do eiusmod tem por incididunt ut labore et dolore magna aliqua. Ut enim ad minim veniam.</p>
  <span class="more-link">Read More →</span>
</div>
<div class="exp-card" style="left:611px">
  <svg width="52" height="56" viewBox="0 0 52 56" fill="none" stroke="#0094d4" stroke-width="2.5"><circle cx="36" cy="10" r="5"/><path d="M30 50V26h12v24M6 50V36h8v14M18 50V28h8v22M6 22l12-10 8 6"/></svg>
  <h3>Experience</h3>
  <p>Lorem ipsum dolor sit amet, consectetur adipiscing elit, sed do eiusmod tem por incididunt ut labore et dolore magna aliqua. Ut enim ad minim veniam.</p>
  <span class="more-link">Read More →</span>
</div>
<div class="exp-card" style="left:875px">
  <svg width="48" height="56" viewBox="0 0 48 56" fill="none" stroke="#0094d4" stroke-width="2.5"><circle cx="24" cy="18" r="8"/><path d="M8 44a16 12 0 0 1 32 0z"/></svg>
  <h3>Expertise</h3>
  <p>Lorem ipsum dolor sit amet, consectetur adipiscing elit, sed do eiusmod tem por incididunt ut labore et dolore magna aliqua. Ut enim ad minim veniam.</p>
  <span class="more-link">Read More →</span>
</div>

<!-- why -->
<section class="why">
  <span class="label">WHY US</span>
  <h2 class="sec-title">Why Choose Us</h2>
  <div class="abs portrait" role="img" aria-label="Smiling businessman in glasses with arms crossed"></div>

  <div class="feat l" style="left:80px;top:2915px"><h3>Quality Services</h3><p>Lorem ipsum dolor sit amet,<br>consectetur adipiscing elit</p></div>
  <div class="ficon" style="left:355px;top:2906px"><svg width="30" height="30" viewBox="0 0 30 30" fill="none" stroke="#0094d4" stroke-width="2"><circle cx="15" cy="6" r="3"/><path d="M5 12h20M15 12v7l-6 8M15 19l6 8"/></svg></div>

  <div class="feat l" style="left:45px;top:3040px"><h3>Client-centric</h3><p>Lorem ipsum dolor sit amet,<br>consectetur adipiscing elit</p></div>
  <div class="ficon" style="left:320px;top:3031px"><svg width="30" height="30" viewBox="0 0 30 30" fill="none" stroke="#0094d4" stroke-width="2" stroke-dasharray="3 3"><circle cx="15" cy="15" r="11"/></svg></div>

  <div class="feat l" style="left:70px;top:3165px"><h3>Personalized Approach</h3><p>Lorem ipsum dolor sit amet,<br>consectetur adipiscing elit</p></div>
  <div class="ficon" style="left:355px;top:3156px"><svg width="30" height="30" viewBox="0 0 30 30" fill="none" stroke="#0094d4" stroke-width="2"><path d="M6 18a9 9 0 0 1 18 0v6H6z"/><path d="M6 18h18"/></svg></div>

  <div class="ficon" style="left:762px;top:2906px"><svg width="30" height="30" viewBox="0 0 30 30" fill="none" stroke="#0094d4" stroke-width="2"><circle cx="15" cy="15" r="11"/><circle cx="15" cy="15" r="6"/><circle cx="15" cy="15" r="2"/></svg></div>
  <div class="feat" style="left:892px;top:2915px"><h3>Customization</h3><p>Lorem ipsum dolor sit amet,<br>consectetur adipiscing elit</p></div>

  <div class="ficon" style="left:797px;top:3031px"><svg width="30" height="30" viewBox="0 0 30 30" fill="none" stroke="#0094d4" stroke-width="2"><path d="M6 18a9 9 0 0 1 18 0v6H6z"/><circle cx="15" cy="12" r="3"/></svg></div>
  <div class="feat" style="left:900px;top:3040px"><h3>Innovative Solutions</h3><p>Lorem ipsum dolor sit amet,<br>consectetur adipiscing elit</p></div>

  <div class="ficon" style="left:762px;top:3156px"><svg width="30" height="30" viewBox="0 0 30 30" fill="none" stroke="#0094d4" stroke-width="2"><rect x="4" y="4" width="6" height="6"/><rect x="20" y="4" width="6" height="6"/><rect x="4" y="20" width="6" height="6"/><rect x="20" y="20" width="6" height="6"/><path d="M10 7h10M10 23h10M7 10v10M23 10v10"/></svg></div>
  <div class="feat" style="left:877px;top:3165px"><h3>Proven Track Record</h3><p>Lorem ipsum dolor sit amet,<br>consectetur adipiscing elit</p></div>
</section>

<!-- testimonials -->
<section class="abs reviews">
  <span class="label">TESTIMONIALS</span>
  <h2 class="sec-title">Client Reviews</h2>
  <div class="rev" style="left:93px">
    <svg class="q" width="36" height="26" viewBox="0 0 36 26" fill="#00a9dd"><path d="M0 0h15v14l-6 12H3l5-10H0zM20 0h15v14l-6 12h-6l5-10h-8z"/></svg>
    <p>Lorem ipsum dolor sit amet, consectetur adipiscing elit, sed do eiusmod tem por incididunt ut labore et dolore magna aliqua. Ut enim ad minim veniam, q uis nostrud exercitation ullamco laboris</p>
    <div class="who"><div class="av" role="img" aria-label="Client portrait"></div><div><b>Niall P.</b><small>Brussels</small></div></div>
  </div>
  <div class="rev" style="left:441px">
    <svg class="q" width="36" height="26" viewBox="0 0 36 26" fill="#00a9dd"><path d="M0 0h15v14l-6 12H3l5-10H0zM20 0h15v14l-6 12h-6l5-10h-8z"/></svg>
    <p>Lorem ipsum dolor sit amet, consectetur adipiscing elit, sed do eiusmod tem por incididunt ut labore et dolore magna aliqua. Ut enim ad minim veniam, q uis nostrud exercitation ullamco laboris</p>
    <div class="who"><div class="av" role="img" aria-label="Client portrait"></div><div><b>Niall P.</b><small>Brussels</small></div></div>
  </div>
  <div class="rev" style="left:788px">
    <svg class="q" width="36" height="26" viewBox="0 0 36 26" fill="#00a9dd"><path d="M0 0h15v14l-6 12H3l5-10H0zM20 0h15v14l-6 12h-6l5-10h-8z"/></svg>
    <p>Lorem ipsum dolor sit amet, consectetur adipiscing elit, sed do eiusmod tem por incididunt ut labore et dolore magna aliqua. Ut enim ad minim veniam, q uis nostrud exercitation ullamco laboris</p>
    <div class="who"><div class="av" role="img" aria-label="Client portrait"></div><div><b>Niall P.</b><small>Brussels</small></div></div>
  </div>
  <div class="abs dots"><span></span><span></span><span class="on"></span><span></span><span></span></div>
</section>

<!-- contact -->
<section class="contact">
  <h2>Get in touch with us</h2>
  <div class="c-item" style="top:4060px">
  <svg width="40" height="36" viewBox="0 0 40 36" fill="none" stroke="#0094d4" stroke-width="1.6"><path d="M20 24s-8-8-8-14a8 8 0 0 1 16 0c0 6-8 14-8 14z"/><circle cx="20" cy="10" r="3"/><path d="M4 34l6-12h20l6 12z"/></svg>
    <div><b>HEAD OFFICE</b><small>21 Lorem Ipsum, ABC 123</small></div></div>
  <div class="c-item" style="top:4133px">
  <svg width="40" height="36" viewBox="0 0 40 36" fill="none" stroke="#0094d4" stroke-width="1.6"><rect x="6" y="8" width="28" height="22"/><path d="M6 8l14 12 14-12"/></svg>
    <div><b>EMAIL ADDRESS</b><small>21 Lorem Ipsum, ABC 123</small></div></div>
  <div class="c-item" style="top:4198px">
  <svg width="40" height="36" viewBox="0 0 40 36" fill="none" stroke="#0094d4" stroke-width="1.6"><rect x="12" y="4" width="16" height="28" rx="2"/><path d="M18 27h4"/></svg>
    <div><b>CALL US NOW</b><small>21 Lorem Ipsum, ABC 123</small></div></div>
</section>
<svg class="abs footer-wave" width="1200" height="175" viewBox="0 0 1200 175">
  <path d="M0 155 Q600 90 1200 30 V175 H0Z" fill="#101a44"/>
  <path d="M505 105 Q850 40 1200 20 V0 Q860 10 505 105Z" fill="#0094d4"/>
</svg>
<div class="abs form">
  <h3>Send Us A Message</h3>
  <div class="field" style="left:38px;top:112px;width:198px"><label>First Name</label><div class="box">John</div></div>
  <div class="field" style="left:251px;top:112px;width:198px"><label>Last Name</label><div class="box">Doe</div></div>
  <div class="field" style="left:38px;top:200px;width:415px"><label>Email</label><div class="box">hello@tallomex-sample.com</div></div>
  <div class="field" style="left:38px;top:290px;width:415px"><label>Message</label><div class="box area">Type Your Message</div></div>
  <div class="btn form-btn">Contact us
    <svg width="16" height="12" viewBox="0 0 16 12" fill="none" stroke="#fff" stroke-width="1.8"><path d="M1 6h13M9 1l5 5-5 5"/></svg>
  </div>
</div>

<!-- footer -->
<footer class="abs footer">
  <div class="abs foot-brand"><div class="brand">Tallomex<i></i></div></div>
  <div class="f-item" style="left:430px">
    <svg width="30" height="30" viewBox="0 0 30 30" fill="none" stroke="#fff" stroke-width="1.5"><circle cx="15" cy="15" r="12"/><ellipse cx="15" cy="15" rx="5" ry="12"/><path d="M3 15h24"/></svg>
    <span>48, Harbour Row, Quay Lane<br>City, State XY 123456</span></div>
  <div class="f-item" style="left:688px">
    <svg width="30" height="30" viewBox="0 0 30 30" fill="none" stroke="#fff" stroke-width="1.5"><rect x="8" y="3" width="13" height="24" rx="2"/></svg>
    <span>PHONE<br>(555) 010 4477</span></div>
  <div class="f-item" style="left:862px">
    <svg width="30" height="30" viewBox="0 0 30 30" fill="none" stroke="#fff" stroke-width="1.5"><rect x="3" y="7" width="24" height="17"/><path d="M3 7l12 10 12-10"/></svg>
    <span>EMAIL<br>hello@tallomex-sample.com</span></div>
  <div class="abs f-nav"><span>HOME</span><span>SERVICES</span><span>ABOUT US</span><span>TESTIMONIALS</span><span>BLOG</span><span>CONTACT US</span></div>
  <span class="abs copy">Tallomex</span>
  <div class="abs f-social"><span></span><span></span><span></span><span></span></div>
</footer>

</body>
</html>
```